Executive Business Card for Healthcare Company [Need Today]

I need a business card design for a healthcare company. The only branding the company has thus far is a logo. The cards will be utilized by company executives. The design I envision will be vibrant and appealing but with a corporate feel. They shouldn't be too casual or playful. I would like to complete this project TODAY if possible.

Target Market(s)

Healthcare vendors, other executives in healthcare and pharmaceuticals

Industry/Entity Type

Pharmaceutical

Contact Information for Business Card

See attachment

Font styles to use
Serif
Sans Serif

Colors

Designer to choose colors to be used in the design.

```html
<!DOCTYPE html>
<html lang="en">
<head>
<meta charset="utf-8">
<title>Corvane Therapeutics – Business Card</title>
<link rel="stylesheet" href="https://fonts.googleapis.com/css2?family=Crimson+Text:wght@400;600&family=Open+Sans:wght@300;400&display=swap">
<style>
  :root {
    --backdrop: #8fa6ad;
    --paper: #ffffff;
    --teal: #2fc1cc;
    --green: #6cc895;
    --ink: #1e1e1e;
    --icon-dark: #222a2b;
    --mist: #cfcfcf;
    --serif: "Crimson Text", Georgia, serif;
    --sans: "Open Sans", Arial, sans-serif;
  }
  html, body { margin: 0; padding: 0; overflow: hidden; }
  body { width: 1200px; height: 800px; background: var(--backdrop); position: relative; }

  .card { position: absolute; left: 326px; width: 538px; height: 306px; background: var(--paper); overflow: hidden; }
  .card--front { top: 24px; }
  .card--back { top: 426px; }

  /* front */
  .card-frame { position: absolute; inset: 0; padding: 8px; background: linear-gradient(135deg, var(--green), var(--teal)); }
  .card-frame-inner { width: 100%; height: 100%; background: var(--paper); }
  .brand { position: absolute; }
  .brand-mark { position: absolute; border-radius: 50%; border-style: solid; border-color: var(--green); box-sizing: border-box; }
  .brand-rule { position: absolute; width: 1px; background: #9a9a9a; }
  .brand-name { position: absolute; font-family: var(--sans); font-weight: 300; color: var(--teal); white-space: nowrap; line-height: 1; }

  .front-brand .brand-mark { left: 70px; top: 50px; width: 128px; height: 128px; border-width: 6px; }
  .front-brand .brand-rule { left: 213px; top: 90px; height: 64px; }
  .front-brand .brand-name--main { left: 228px; top: 78px; font-size: 52px; }
  .front-brand .brand-name--sub { left: 318px; top: 136px; font-size: 26px; }

  .social { position: absolute; left: 0; right: 0; top: 198px; text-align: center; }
  .social-title { font-family: var(--serif); font-size: 17px; color: var(--ink); margin: 0 0 6px; }
  .social-icons { display: flex; justify-content: center; gap: 8px; }
  .social-icon { width: 18px; height: 18px; background: var(--teal); border-radius: 3px; }
  .front-web { position: absolute; left: 0; right: 0; top: 278px; text-align: center; font-family: var(--serif); font-size: 13px; color: var(--teal); }

  /* back */
  .person { position: absolute; left: 27px; top: 26px; }
  .person-name { font-family: var(--serif); font-size: 38px; font-weight: 400; color: var(--ink); margin: 0; line-height: 1; }
  .person-title { font-family: var(--serif); font-size: 18px; color: var(--ink); margin: 8px 0 0 1px; }

  .back-brand .brand-mark { left: 296px; top: 23px; width: 70px; height: 70px; border-width: 4px; }
  .back-brand .brand-rule { left: 374px; top: 46px; height: 33px; }
  .back-brand .brand-name--main { left: 382px; top: 44px; font-size: 27px; }
  .back-brand .brand-name--sub { left: 430px; top: 72px; font-size: 15px; }

  .backdrop-mark { position: absolute; left: 348px; top: 131px; width: 184px; height: 184px; border: 8px solid var(--mist); border-radius: 50%; box-sizing: border-box; }

  .contact { position: absolute; left: 26px; display: flex; align-items: center; gap: 10px; }
  .contact-icon { width: 26px; height: 26px; flex: none; }
  .contact-text { font-family: var(--sans); font-size: 17px; color: var(--ink); }
  .contact--mobile { top: 119px; }
  .contact--office { top: 159px; }
  .contact--email { top: 197px; }
  .contact--email .contact-text { font-size: 16px; }
  .contact--address { top: 238px; align-items: flex-start; gap: 4px; }
  .contact--address .contact-text { font-family: var(--serif); font-size: 15px; line-height: 20px; }

  .footer-bar { position: absolute; top: 293px; height: 6px; background: linear-gradient(90deg, var(--teal), var(--green)); }
  .footer-bar--left { left: 0; width: 190px; }
  .footer-bar--right { left: 346px; width: 192px; }
  .back-web { position: absolute; left: 190px; width: 156px; top: 284px; text-align: center; font-family: var(--serif); font-size: 14px; color: var(--ink); }
</style>
</head>
<body>

<section class="card card--front" aria-label="Card front">
  <div class="card-frame"><div class="card-frame-inner"></div></div>
  <div class="brand front-brand">
    <span class="brand-mark"></span>
    <span class="brand-rule"></span>
    <span class="brand-name brand-name--main">corvane</span>
    <span class="brand-name brand-name--sub">therapeutics</span>
  </div>
  <div class="social">
    <p class="social-title">Find Us on:</p>
    <div class="social-icons" role="img" aria-label="Social network links">
      <span class="social-icon"></span><span class="social-icon"></span><span class="social-icon"></span><span class="social-icon"></span>
    </div>
  </div>
  <div class="front-web">www.website.com</div>
</section>

<section class="card card--back" aria-label="Card back">
  <span class="backdrop-mark"></span>

  <div class="person">
    <h1 class="person-name">Daniel Marsh</h1>
    <p class="person-title">Senior Director of Marketing</p>
  </div>

  <div class="brand back-brand">
    <span class="brand-mark"></span>
    <span class="brand-rule"></span>
    <span class="brand-name brand-name--main">corvane</span>
    <span class="brand-name brand-name--sub">therapeutics</span>
  </div>

  <div class="contact contact--mobile">
    <svg class="contact-icon" viewBox="0 0 26 26" aria-hidden="true"><circle cx="13" cy="13" r="13" fill="var(--icon-dark)"/><path d="M9 7.5l2.2-.6 1.3 3-1.4 1.1c.7 1.5 1.8 2.6 3.3 3.3l1.1-1.4 3 1.3-.6 2.2c-5.2.3-9.2-3.7-8.9-8.9z" fill="#fff"/></svg>
    <span class="contact-text">555-201-4837</span>
  </div>
  <div class="contact contact--office">
    <svg class="contact-icon" viewBox="0 0 26 26" aria-hidden="true"><circle cx="13" cy="13" r="13" fill="var(--icon-dark)"/><path d="M6 11c0-3 14-3 14 0v1.5h-3.5V10.8h-7v1.7H6z" fill="#fff"/><rect x="8.5" y="12.5" width="9" height="6" rx="1" fill="#fff"/><circle cx="13" cy="15.5" r="1.6" fill="var(--icon-dark)"/></svg>
    <span class="contact-text">555-201-4900</span>
  </div>
  <div class="contact contact--email">
    <svg class="contact-icon" viewBox="0 0 26 26" aria-hidden="true"><circle cx="13" cy="13" r="13" fill="var(--icon-dark)"/><rect x="7" y="9" width="12" height="8.5" fill="#fff"/><path d="M7 9l6 5 6-5" fill="none" stroke="var(--icon-dark)" stroke-width="1"/></svg>
    <span class="contact-text">dmarsh@corvanerx.com</span>
  </div>
  <div class="contact contact--address">
    <svg class="contact-icon" viewBox="0 0 26 26" aria-hidden="true"><circle cx="13" cy="13" r="13" fill="var(--icon-dark)"/><path d="M13 20.5s-4.5-5-4.5-8.2a4.5 4.5 0 019 0c0 3.2-4.5 8.2-4.5 8.2z" fill="#fff"/><circle cx="13" cy="12.2" r="1.6" fill="var(--icon-dark)"/></svg>
    <span class="contact-text">118 W Linden Avenue Marlow<br>GA 30000</span>
  </div>

  <span class="footer-bar footer-bar--left"></span>
  <span class="back-web">www.website.com</span>
  <span class="footer-bar footer-bar--right"></span>
</section>

</body>
</html>
```